business card for horse saddlery

after a new business card for our saddlery, i will add 2 logos we have previously used and they can be used (or not) . Any images can be used from our website also at www.harrowfields.net.au, I have also added our brand logo, which may be good to incorporate on back ? we have over 15, 000 items online, ship Australia Wide.

Target Market(s)

horse owners

Industry/Entity Type

Retail - Equestrian

Contact Information for Business Card

Harrowfield Horse Supplies, 1300 48 62 90, www.harrowfields.net.au, 27 Lindqvist Rd Marrowbank Q 4587

Requirements
Must have
• trailgem is our brand so trailgem logo on back as 'distributers of', easy to read
Nice to have
• professional but fun
Should not have
• double sided (description wont save double sided)

```html
<!DOCTYPE html>
<html lang="en">
<head>
<meta charset="utf-8">
<title>Harrowfield Horse Supplies – Business Card</title>
<link href="https://fonts.googleapis.com/css2?family=Questrial&display=swap" rel="stylesheet">
<style>
  :root {
    --backdrop: #3a3a3c;
    --card-white: #ffffff;
    --card-mist: #f1f2f4;
    --card-ice: #d9ecf8;
    --navy: #1f4a8c;
    --slate: #3d4146;
    --sky-line: #8fd0ee;
    --icon-blue: #24428a;
  }
  * { margin: 0; padding: 0; box-sizing: border-box; }
  html, body {
    width: 1200px; height: 900px; overflow: hidden;
    background: var(--backdrop);
    font-family: "Questrial", sans-serif;
  }
  .stage {
    width: 1200px; height: 900px;
    display: flex; flex-direction: column; align-items: center; justify-content: center;
    gap: 60px;
  }
  .card {
    position: relative;
    width: 630px; height: 360px;
    border-radius: 40px;
    overflow: hidden;
  }
  .card--front {
    background: radial-gradient(ellipse at 45% 60%, var(--card-white) 40%, var(--card-mist) 70%, var(--card-ice) 100%);
    display: flex; align-items: center; justify-content: center;
  }
  .brand-lockup { text-align: center; color: var(--navy); }
  .brand-lockup__mark {
    width: 64px; height: 64px; border-radius: 50%;
    background: var(--navy);
    margin: 0 auto 18px;
  }
  .brand-lockup__tagline {
    font-size: 15px; letter-spacing: 4px; color: var(--slate);
    margin-bottom: 4px;
  }
  .brand-lockup__name {
    font-size: 48px; letter-spacing: 2px; text-transform: uppercase;
  }
  .card--back {
    background: linear-gradient(160deg, var(--card-mist) 0%, var(--card-white) 45%, var(--card-white) 100%);
  }
  .shop-lockup {
    position: absolute; left: 56px; top: 112px;
    display: flex; align-items: center; gap: 14px;
    color: var(--navy);
  }
  .shop-lockup__mark {
    width: 18px; height: 18px; border-radius: 50%; background: var(--navy);
  }
  .shop-lockup__name { font-size: 24px; }
  .contact {
    position: absolute; right: 40px; top: 128px;
    text-align: right; color: var(--slate);
    font-size: 17px; line-height: 1;
  }
  .contact__row {
    display: flex; justify-content: flex-end; align-items: center; gap: 8px;
    margin-bottom: 14px;
  }
  .contact__icon { width: 16px; height: 16px; flex: none; }
  .contact__rule {
    position: absolute; right: 30px; top: 210px;
    width: 320px; height: 1.5px; background: var(--sky-line);
  }
  .contact__address {
    position: absolute; right: 40px; top: 224px;
    font-size: 17px; color: var(--slate);
    display: flex; align-items: center; gap: 8px;
  }
</style>
</head>
<body>
<main class="stage">
  <section class="card card--front" aria-label="Business card front">
    <div class="brand-lockup">
      <div class="brand-lockup__mark" aria-hidden="true"></div>
      <p class="brand-lockup__tagline">Distributers Of</p>
      <p class="brand-lockup__name">Trailgem</p>
    </div>
  </section>

  <section class="card card--back" aria-label="Business card back">
    <div class="shop-lockup">
      <span class="shop-lockup__mark" aria-hidden="true"></span>
      <span class="shop-lockup__name">harrowfields.net.au</span>
    </div>

    <div class="contact">
      <p class="contact__row">1300 48 62 90
        <svg class="contact__icon" viewBox="0 0 16 16" aria-hidden="true">
          <path d="M2 5c0-2 2-3 6-3s6 1 6 3v1h-3V5H5v1H2z" fill="var(--icon-blue)"/>
          <rect x="3" y="7" width="10" height="7" rx="1.5" fill="var(--icon-blue)"/>
        </svg>
      </p>
      <p class="contact__row">www.harrowfields.net.au
        <svg class="contact__icon" viewBox="0 0 16 16" aria-hidden="true">
          <circle cx="8" cy="8" r="6.5" fill="none" stroke="var(--icon-blue)" stroke-width="1.6"/>
          <path d="M1.5 8h13M8 1.5c-3 3-3 10 0 13M8 1.5c3 3 3 10 0 13" fill="none" stroke="var(--icon-blue)" stroke-width="1.2"/>
        </svg>
      </p>
    </div>
    <div class="contact__rule" aria-hidden="true"></div>
    <p class="contact__address">27 Lindqvist Rd Marrowbank Q 4587
      <svg class="contact__icon" viewBox="0 0 16 16" aria-hidden="true">
        <path d="M8 1a5 5 0 0 0-5 5c0 4 5 9 5 9s5-5 5-9a5 5 0 0 0-5-5z" fill="var(--icon-blue)"/>
        <circle cx="8" cy="6" r="1.8" fill="var(--card-white)"/>
      </svg>
    </p>
  </section>
</main>
</body>
</html>
```